Smile club flyer design

I am launching an office smile club and would like a design that sits my branding and that is appealing to customers. I have a design (I need a new one) that has all the information.
My website is maplehavendentalcarekx.com
Brand color is green. The design can be any color

Target Market(s)

Ages 30+

Industry/Entity Type

Dental

Font styles to use
Serif

Requirements
Must have
• Appealing to patients

```html
<!DOCTYPE html>
<html lang="en">
<head>
<meta charset="utf-8">
<title>Maplehaven Dental Care – Smile Club Membership</title>
<link href="https://fonts.googleapis.com/css2?family=Poppins:wght@500;600;700;800&family=Barlow+Condensed:wght@500;600&family=EB+Garamond:wght@600;700&family=Dancing+Script:wght@700&display=swap" rel="stylesheet">
<style>
:root{
  --stage:#383838;
  --mint-1:#e6f4ea;
  --mint-2:#b8e0c6;
  --mint-3:#9dd4bc;
  --brand:#2a8a4e;
  --brand-deep:#0f7a32;
  --forest:#0d4d27;
  --ink:#2c2c2c;
  --orange:#ea8412;
  --core-head:#3db38a;
  --core-price:#5ccb9f;
  --core-body:#8fd7be;
  --core-line:#36b48a;
  --bright-head:#077a70;
  --bright-price:#0a9e93;
  --bright-body:#9ebcab;
  --bright-line:#0c5f55;
  --total-head:#0a9196;
  --total-price:#08b0b3;
  --total-body:#72c3c4;
  --total-line:#0a7e8a;
  --refresh-head:#8aac74;
  --refresh-price:#a8d28f;
  --refresh-body:#a9c597;
  --refresh-line:#7d9c68;
  --feature-ink:#123a32;
  --tick-core:#22a57a;
  --tick-dark:#0c6a5e;
  --tick-refresh:#5d7f4a;
}
*{box-sizing:border-box;margin:0;padding:0}
html,body{width:1011px;height:1200px;overflow:hidden;background:var(--stage)}
.flyer{
  position:absolute;left:173px;top:101px;width:665px;height:997px;overflow:hidden;
  background:radial-gradient(ellipse at 25% 10%,#f3faf4 0%,transparent 45%),
             linear-gradient(180deg,var(--mint-1) 0%,var(--mint-2) 45%,var(--mint-3) 100%);
  font-family:"Poppins",sans-serif;
}
.hero-photo{
  position:absolute;left:252px;top:0;width:258px;height:157px;
  background:radial-gradient(ellipse at 50% 40%,#f1c9ad 0%,#d98a60 45%,#b9542c 75%,rgba(185,84,44,0) 100%);
}
.brand-name{
  position:absolute;left:420px;top:46px;width:236px;text-align:center;
  font-family:"EB Garamond",serif;font-weight:700;color:var(--brand-deep);
  font-size:30px;line-height:1.05;
}
.brand-name span{display:block;font-size:19px;letter-spacing:3px}
.intro{
  position:absolute;left:68px;top:108px;
  font-family:"Dancing Script",cursive;font-weight:700;font-size:29px;color:var(--forest);
  transform:rotate(4deg);
}
.title-band{
  position:absolute;left:58px;top:156px;width:549px;height:105px;
  background:linear-gradient(180deg,#2f9156,#237a45);
  border-radius:26px 44px 6px 30px;
  display:flex;align-items:center;justify-content:center;
}
.title-band h1{font-weight:800;color:#fff;font-size:80px;letter-spacing:-1px;line-height:1}
.membership{
  position:absolute;left:0;width:100%;top:262px;text-align:center;
  font-weight:700;font-size:55px;color:var(--brand-deep);letter-spacing:-1px;line-height:1.1;
}
.tagline{
  position:absolute;left:0;width:100%;top:322px;text-align:center;
  font-weight:600;font-size:27px;color:var(--ink);line-height:1.2;
}
.plan{position:absolute;top:370px;width:183px;height:294px}
.plan-body{
  position:absolute;left:6px;right:6px;top:125px;bottom:0;
  border-radius:0 0 12px 12px;border:2px solid;border-top:none;
  box-shadow:0 0 10px rgba(255,255,255,.8);
}
.plan-head{
  position:absolute;left:0;top:0;width:100%;height:152px;border-radius:10px 10px 0 0;
  clip-path:polygon(0 0,100% 0,100% 80%,50% 100%,0 80%);
  text-align:center;color:#fff;
}
.plan-head h2{font-weight:700;font-size:22px;line-height:1;margin-top:21px;letter-spacing:-.2px}
.plan-head p{font-weight:500;font-size:14px;line-height:1.2;margin-top:2px}
.price{
  margin:9px auto 0;width:139px;height:56px;border-radius:4px 4px 0 0;
  clip-path:polygon(0 0,100% 0,100% 88%,50% 100%,0 88%);
  display:flex;flex-direction:column;align-items:center;justify-content:center;
}
.price strong{font-weight:800;font-size:36px;line-height:.95}
.price small{font-weight:500;font-size:11px;line-height:1}
.features{position:absolute;left:12px;right:6px;list-style:none;
  font-family:"Barlow Condensed",sans-serif;font-weight:600;font-size:10.5px;color:var(--feature-ink);line-height:1.2}
.features li{display:flex;gap:5px;margin-bottom:9px}
.features svg{flex:none;width:10px;height:10px;margin-top:2px}
.plan--core{left:42px}
.plan--core .plan-head{background:var(--core-head)}
.plan--core .price{background:var(--core-price)}
.plan--core .plan-body{background:var(--core-body);border-color:var(--core-line)}
.plan--core .features{top:180px;color:#0c4d3c}
.plan--core svg{color:var(--tick-core)}
.plan--bright{left:245px}
.plan--bright .plan-head{background:var(--bright-head)}
.plan--bright .price{background:var(--bright-price)}
.plan--bright .plan-body{background:var(--bright-body);border-color:var(--bright-line)}
.plan--bright .features{top:180px}
.plan--bright svg{color:var(--tick-dark)}
.plan--total{left:448px}
.plan--total .plan-head{background:var(--total-head)}
.plan--total .price{background:var(--total-price)}
.plan--total .plan-body{background:var(--total-body);border-color:var(--total-line)}
.plan--total .features{top:169px}
.plan--total svg{color:var(--tick-dark)}
.join-band{position:absolute;left:0;top:695px;width:100%;height:127px;background:#fff}
.join-title{
  position:absolute;left:40px;top:718px;
  font-family:"EB Garamond",serif;font-weight:700;font-size:40px;color:var(--forest);line-height:1;
}
.join-phone{
  position:absolute;left:72px;top:762px;
  font-family:"EB Garamond",serif;font-weight:700;font-size:47px;color:var(--orange);line-height:1;letter-spacing:.5px;
}
.plan--refresh{left:448px;top:689px;height:295px}
.plan--refresh .plan-head{background:var(--refresh-head);height:153px}
.plan--refresh .plan-head h2{margin-top:20px}
.plan--refresh .price{background:var(--refresh-price);height:54px;margin-top:9px}
.plan--refresh .price strong{font-size:36px}
.plan--refresh .plan-body{background:var(--refresh-body);border-color:var(--refresh-line)}
.plan--refresh .features{top:160px;font-size:13px;left:14px;color:#15331c}
.plan--refresh .features li{margin-bottom:7px}
.plan--refresh svg{color:var(--tick-refresh);margin-top:3px}
.offer{
  position:absolute;left:0;width:100%;top:226px;text-align:center;
  font-family:"EB Garamond",serif;font-weight:700;font-size:29px;line-height:1;color:var(--forest);
}
.financing{
  position:absolute;left:22px;top:853px;
  font-weight:600;font-size:20.5px;color:var(--ink);letter-spacing:-.2px;
}
.lender{
  position:absolute;left:99px;top:886px;display:flex;align-items:center;gap:10px;
  font-weight:700;font-size:38px;color:#17233a;line-height:1;
}
.lender i{display:block;width:50px;height:50px;border-radius:50%;background:#17233a}
.fee-note{
  position:absolute;left:37px;top:951px;
  font-weight:500;font-size:14.5px;color:var(--forest);
}
</style>
</head>
<body>
<svg width="0" height="0" style="position:absolute">
  <symbol id="tick" viewBox="0 0 10 10">
    <circle cx="5" cy="5" r="5" fill="currentColor"/>
    <path d="M2.8 5.2 4.4 6.7 7.3 3.6" fill="none" stroke="#fff" stroke-width="1.3" stroke-linecap="round" stroke-linejoin="round"/>
  </symbol>
</svg>

<main class="flyer">
  <div class="hero-photo" role="img" aria-label="Smiling young woman pointing at her smile"></div>
  <div class="brand-name">Maplehaven<span>DENTAL CARE</span></div>
  <div class="intro">Introducing</div>

  <div class="title-band"><h1>SMILE CLUB</h1></div>
  <div class="membership">MEMBERSHIP</div>
  <div class="tagline">NO INSURANCE? NO PROBLEM</div>

  <section class="plan plan--core">
    <div class="plan-body"></div>
    <div class="plan-head">
      <h2>CORE CARE</h2><p>PREVENTIVE</p>
      <div class="price"><strong>$39</strong><small>/MONTH</small></div>
    </div>
    <ul class="features">
      <li><svg><use href="#tick"/></svg>Comprehensive Annual Exam</li>
      <li><svg><use href="#tick"/></svg>2 Professional Cleanings per Year</li>
      <li><svg><use href="#tick"/></svg>Routine Bitewing X-rays</li>
      <li><svg><use href="#tick"/></svg>10% Savings on Treatment</li>
    </ul>
  </section>

  <section class="plan plan--bright">
    <div class="plan-body"></div>
    <div class="plan-head">
      <h2>BRIGHT</h2><p>COSMETIC</p>
      <div class="price"><strong>$59</strong><small>/MONTH</small></div>
    </div>
    <ul class="features">
      <li><svg><use href="#tick"/></svg>Annual In-Office Whitening<br>(Top &amp; Bottom)</li>
      <li><svg><use href="#tick"/></svg>Custom Whitening Trays</li>
      <li><svg><use href="#tick"/></svg>15% Savings on Elective Treatment</li>
    </ul>
  </section>

  <section class="plan plan--total">
    <div class="plan-body"></div>
    <div class="plan-head">
      <h2>TOTAL SMILE</h2><p>PERIODONTAL</p>
      <div class="price"><strong>$89</strong><small>/MONTH</small></div>
    </div>
    <ul class="features">
      <li><svg><use href="#tick"/></svg>3-4 Perio Maintenance<br>Visits per Year</li>
      <li><svg><use href="#tick"/></svg>1 Comprehensive Exam</li>
      <li><svg><use href="#tick"/></svg>Diagnostic X-rays</li>
      <li><svg><use href="#tick"/></svg>15% Savings on Restorative &amp;<br>Elective Care</li>
    </ul>
  </section>

  <div class="join-band"></div>
  <div class="join-title">Join Smile Club Today!</div>
  <div class="join-phone">555-014-2368</div>

  <section class="plan plan--refresh">
    <div class="plan-body"></div>
    <div class="plan-head">
      <h2>SMILE</h2><p>REFRESH PACKAGE</p>
      <div class="price"><strong>$499</strong></div>
    </div>
    <ul class="features">
      <li><svg><use href="#tick"/></svg>Cleaning</li>
      <li><svg><use href="#tick"/></svg>Comprehensive Exam</li>
      <li><svg><use href="#tick"/></svg>Whitening</li>
    </ul>
    <div class="offer">Limited<br>Time Offer</div>
  </section>

  <div class="financing">FLEXIBLE FINANCING FOR TREATMENT</div>
  <div class="lender"><i></i>Petalpay</div>
  <div class="fee-note">*$49 Lifetime Activation Fee (Non-Refundable)</div>
</main>
</body>
</html>
```